Tech business card design

We need an amazing business card design for our new business 'Pexla' a marketing tech startup based in Sydney, Australia. We provide an online marketplace for businesses to search and buy advertising media, connect with service providers and learn more about marketing. We wish to communicate 'cool tech', reliability and professionalism and design based around our logo.

Target Market(s)

Business Owners

Contact Information for Business Card

Name
Position
Email Address
Website
Phone Number

Font styles to use
Other font styles liked:
• Avenir & Avenir Next

Colors

Designer to choose colors to be used in the design.

```html
<!DOCTYPE html>
<html lang="en">
<head>
<meta charset="utf-8">
<title>Pexla – Business Card</title>
<link rel="stylesheet" href="https://fonts.googleapis.com/css2?family=Nunito+Sans:wght@400;800&display=swap">
<style>
  :root {
    --backdrop: #dfe1e8;
    --navy: #0f1b47;
    --paper: #ffffff;
    --sheen: #eef0f4;
    --ink-light: #ffffff;
    --shadow: rgba(20, 28, 60, 0.18);
  }
  html, body {
    margin: 0;
    width: 1200px;
    height: 797px;
    overflow: hidden;
    background: var(--backdrop);
    font-family: "Nunito Sans", Avenir, "Avenir Next", sans-serif;
  }
  .stage {
    position: relative;
    width: 1200px;
    height: 797px;
  }
  .card {
    position: absolute;
    width: 504px;
    height: 288px;
    top: 254px;
    border-radius: 2px;
    box-shadow: 0 10px 28px var(--shadow);
    overflow: hidden;
  }
  .card--back {
    left: 64px;
    background: var(--paper);
  }
  .card--front {
    left: 632px;
    background: var(--navy);
    color: var(--ink-light);
  }
  .card-back__sweep {
    position: absolute;
    inset: 0;
  }
  .wordmark {
    position: absolute;
    font-weight: 800;
    letter-spacing: -0.02em;
    line-height: 1;
  }
  .card--back .wordmark {
    color: var(--navy);
    font-size: 92px;
    left: 50%;
    top: 50%;
    transform: translate(-50%, -58%);
  }
  .card--front .wordmark {
    color: var(--ink-light);
    font-size: 78px;
    left: 34px;
    bottom: 40px;
  }
  .contact {
    position: absolute;
    left: 262px;
    top: 40px;
  }
  .contact__name {
    font-size: 21px;
    font-weight: 400;
    letter-spacing: 0.04em;
    margin: 0;
  }
  .contact__role {
    font-size: 12px;
    margin: 2px 0 14px;
  }
  .contact__list {
    list-style: none;
    margin: 0;
    padding: 0;
    font-size: 12.5px;
  }
  .contact__item {
    display: flex;
    align-items: center;
    gap: 7px;
    margin-bottom: 5px;
  }
  .contact__icon {
    width: 13px;
    height: 13px;
    flex: none;
  }
</style>
</head>
<body>
<main class="stage">
  <section class="card card--back" aria-label="Card back">
    <svg class="card-back__sweep" viewBox="0 0 504 288" aria-hidden="true">
      <path d="M0 288 L0 205 C150 150 330 140 504 165 L504 288 Z" fill="var(--sheen)"/>
    </svg>
    <span class="wordmark">pexla</span>
  </section>

  <section class="card card--front" aria-label="Card front">
    <span class="wordmark">pexla</span>
    <div class="contact">
      <h1 class="contact__name">MARCUS HALE</h1>
      <p class="contact__role">Managing Director</p>
      <ul class="contact__list">
        <li class="contact__item">
          <svg class="contact__icon" viewBox="0 0 13 13" aria-hidden="true">
            <rect width="13" height="13" rx="2" fill="#fff"/>
            <path d="M4 3h1.6l.7 1.8-1 .7a5 5 0 0 0 2.2 2.2l.7-1 1.8.7V10c-3.6.2-6.3-2.6-6-7z" fill="var(--navy)"/>
          </svg>
          000-555-0142
        </li>
        <li class="contact__item">
          <svg class="contact__icon" viewBox="0 0 13 13" aria-hidden="true">
            <rect width="13" height="13" rx="2" fill="#fff"/>
            <rect x="2.5" y="4" width="8" height="5.5" fill="none" stroke="var(--navy)" stroke-width="1"/>
            <path d="M2.5 4l4 3 4-3" fill="none" stroke="var(--navy)" stroke-width="1"/>
          </svg>
          info@pexlamail.com
        </li>
        <li class="contact__item">
          <svg class="contact__icon" viewBox="0 0 13 13" aria-hidden="true">
            <rect width="13" height="13" rx="2" fill="#fff"/>
            <circle cx="6.5" cy="6.5" r="4" fill="none" stroke="var(--navy)" stroke-width="1"/>
            <path d="M2.5 6.5h8M6.5 2.5c-2 2.4-2 5.6 0 8M6.5 2.5c2 2.4 2 5.6 0 8" fill="none" stroke="var(--navy)" stroke-width="0.8"/>
          </svg>
          www.pexlamail.com
        </li>
      </ul>
    </div>
  </section>
</main>
</body>
</html>
```